Brightfield Ventures Inc. Letterhead

Creation of attractive and eye catching letterhead for a business start-up for the construction industry. Letterhead must relate to construction, but avoid standard hammer and tools in the design.

I forgot to add some details, sorry about that. Some pertinent info: Ph: 916-555-0187 brightfieldventures.example 448 Willowmere Ave, Ste 210 Folsom, CA 95999 info@brightfieldventures.example not sure if slogan should be in there" “Connecting construction professionals to create a purpose driven industry.” must be able to be used in word. Thanks!

```html
<!DOCTYPE html>
<html lang="en">
<head>
<meta charset="utf-8">
<title>Brightfield Ventures Inc. Letterhead</title>
<link href="https://fonts.googleapis.com/css2?family=Open+Sans:wght@400;600;700&display=swap" rel="stylesheet">
<style>
  :root {
    --bg: #cfcfcf;
    --paper: #ffffff;
    --navy: #0f1b3d;
    --red: #c8202f;
    --ink: #3a3a3a;
    --muted: #555a63;
    --white: #ffffff;
  }
  * { box-sizing: border-box; margin: 0; padding: 0; }
  html, body {
    width: 1200px; height: 795px; overflow: hidden;
    background: var(--bg);
    font-family: "Open Sans", Arial, sans-serif;
  }
  .letterhead {
    position: absolute; left: 333px; top: 20px;
    width: 534px; height: 755px;
    background: var(--paper);
    box-shadow: 0 4px 14px rgba(0,0,0,.18);
    overflow: hidden;
  }
  .website {
    position: absolute; top: 20px; right: 34px;
    font-size: 7.5px; font-weight: 600; color: var(--red);
  }
  .header-rule {
    position: absolute; top: 62px; height: 1px; background: var(--red);
  }
  .header-rule.left { left: 0; width: 175px; }
  .header-rule.right { right: 0; width: 175px; }
  .brand {
    position: absolute; top: 48px; left: 0; right: 0;
    text-align: center;
    font-size: 12px; font-weight: 700; color: var(--navy);
    line-height: 28px;
  }
  .letter {
    position: absolute; left: 40px; top: 128px; right: 40px;
    font-size: 7.6px; line-height: 1.45; color: var(--ink);
  }
  .date { margin-bottom: 8px; }
  .recipient { margin-bottom: 10px; }
  .salutation { font-weight: 700; margin-bottom: 12px; }
  .letter p.body { margin-bottom: 12px; color: var(--muted); }
  .signoff {
    position: absolute; right: 40px; top: 372px;
    font-size: 7.6px; color: var(--ink); width: 92px;
  }
  .signature {
    margin-top: 6px; width: 82px; height: 24px;
    background: linear-gradient(90deg, #f2f2f2, #e6e6e6);
  }
  .footer { position: absolute; left: 0; bottom: 0; width: 534px; height: 140px; }
  .footer svg { position: absolute; inset: 0; }
  .footer-info {
    position: absolute; left: 18px; bottom: 10px;
    font-size: 8px; line-height: 1.45; color: var(--white);
  }
  .footer-info .company { color: var(--red); font-weight: 700; font-size: 9px; }
  .contact-row { display: flex; gap: 10px; align-items: center; }
  .contact-row span { display: inline-flex; align-items: center; gap: 4px; }
</style>
</head>
<body>
  <main class="letterhead">
    <div class="website">www.brightfieldventures.example</div>
    <div class="header-rule left"></div>
    <div class="header-rule right"></div>
    <div class="brand">Brightfield Ventures Inc.</div>

    <section class="letter">
      <div class="date">January 12, 2014</div>
      <div class="recipient">Mr. John Doe<br>President<br>AA Corporation<br>111 Street Name, Suite#<br>City, State, 12345</div>
      <div class="salutation">Dear Mr. John,</div>
      <p class="body">Lorem Ipsum is simply dummy text of the printing and typesetting industry. Lorem Ipsum has been the industry's standard dummy text ever since the 1500s, when an unknown printer took a galley of type and scrambled it to make a type specimen book. It has survived not only five centuries, but also the leap into electronic typesetting, remaining essentially unchanged.</p>
      <p class="body">The standard chunk of Lorem Ipsum used since the 1500s is reproduced below for those interested. Sections 1.10.32 and 1.10.33 from "de Finibus Bonorum et Malorum" by Cicero are also reproduced in their exact original form, accompanied by English versions from the 1914 translation by H. Whitcombe.</p>
      <p class="body">Lorem Ipsum is simply dummy text of the printing and typesetting industry. Lorem Ipsum has been the industry's standard dummy text ever since the 1500s, when an unknown printer took a galley of type and scrambled it to make a type specimen book. It has survived not only five centuries, but also the leap into electronic typesetting, remaining essentially unchanged. It was popularised in the</p>
    </section>

    <div class="signoff">
      Sincerely Your,
      <div class="signature" role="img" aria-label="Handwritten signature"></div>
    </div>

    <footer class="footer">
      <svg width="534" height="140" viewBox="0 0 534 140" aria-hidden="true">
        <polygon points="0,85 430,85 385,140 0,140" fill="var(--navy)"/>
        <polygon points="470,20 534,20 534,140 385,140" fill="var(--red)"/>
      </svg>
      <div class="footer-info">
        <div class="company">Brightfield Ventures Inc.</div>
        <div>448 Willowmere Ave, Ste 210, Folsom, CA 95999</div>
        <div class="contact-row">
          <span>
            <svg width="8" height="8" viewBox="0 0 10 10"><circle cx="5" cy="5" r="5" fill="var(--red)"/><path d="M3 2.5l1 1-.6.8a4 4 0 0 0 2.3 2.3l.8-.6 1 1-.7.9C4.6 7.7 2.3 5.4 2.1 3.2z" fill="#fff"/></svg>
            916-555-0187
          </span>
          <span>
            <svg width="8" height="8" viewBox="0 0 10 10"><circle cx="5" cy="5" r="5" fill="var(--red)"/><rect x="2.4" y="3.2" width="5.2" height="3.6" fill="#fff"/><path d="M2.4 3.2L5 5.3 7.6 3.2" stroke="var(--red)" stroke-width=".6" fill="none"/></svg>
            info@brightfieldventures.example
          </span>
        </div>
      </div>
    </footer>
  </main>
</body>
</html>
```